"Vine Hollow Excursions" is a top notch Santa Barbara County Wine Tour company.

We provide scenic, boutique and custom wine tours. I need the card to be clean and classy. I will provide our logo. I would like the logo to cover the back side of the card as an option and would like to see a couple color options other then our signature green and gold. I would like to see some creative options and let the designers come up with options.
I need cards for myself and my team. The final design should communicate "An authentic and boutique wine tour experience"
Please use my website for reference www.vinehollowexcursions.example

Target Market(s)

We have a wide range of clients from millennials to baby boomers

Industry/Entity Type

Tour

Contact Information for Business Card

Contact info:
Dale Morton
805-219-6384
info@vinehollowexcursions.example
vinehollowexcursions.example

Colors

Designer to choose colors to be used in the design.

Requirements
Must have
• my logo
Nice to have
• *I would like to have the backside side with the logo and the company statement
• "An authentic and boutique wine tour experience" as an option.
• *I would also like to see what the designers can create!
• *I would like to see an option that incorporates or social: instagram, yelp, trip advisor
Should not have
• I do not want it too busy.

```html
<!DOCTYPE html>
<html lang="en">
<head>
<meta charset="utf-8">
<title>Vine Hollow Excursions — Business Card</title>
<link rel="stylesheet" href="https://fonts.googleapis.com/css2?family=Open+Sans:wght@400;600&display=swap">
<style>
  :root {
    --canvas: #dcd9d5;
    --frost: #f2f0ee;
    --frost-edge: #e6e3e0;
    --vine-green: #2b6a46;
    --paper-white: #ffffff;
    --ink-green: #2b6a46;
  }
  * { margin: 0; padding: 0; box-sizing: border-box; }
  html, body {
    width: 1200px; height: 900px; overflow: hidden;
    background: var(--canvas);
    font-family: "Open Sans", Arial, sans-serif;
  }
  .card {
    position: absolute; left: 266px; top: 243px;
    width: 667px; height: 414px;
  }
  .card-shape { position: absolute; inset: 0; }
  .holder { position: absolute; left: 32px; top: 34px; color: var(--paper-white); }
  .holder-name { font-size: 25px; font-weight: 400; line-height: 1.2; }
  .holder-title { font-size: 16px; font-weight: 400; margin-top: 2px; }
  .contacts {
    position: absolute; left: 32px; top: 316px;
    list-style: none; color: var(--paper-white);
    font-size: 13.5px; line-height: 24px;
  }
  .contacts li { display: flex; align-items: center; gap: 9px; white-space: nowrap; }
  .contacts svg { width: 13px; height: 13px; flex: none; fill: var(--paper-white); }
  .brand {
    position: absolute; left: 300px; width: 330px; top: 140px;
    text-align: center; color: var(--ink-green);
  }
  .brand-dot {
    display: block; width: 46px; height: 46px; margin: 0 auto 18px;
    border-radius: 50%; background: var(--vine-green);
  }
  .brand-name {
    font-size: 30px; font-weight: 400; line-height: 1.15;
    letter-spacing: 1px; text-transform: uppercase;
  }
</style>
</head>
<body>
  <div class="card">
    <svg class="card-shape" viewBox="0 0 667 414" width="667" height="414" aria-hidden="true">
      <defs>
        <clipPath id="card-outline">
          <path d="M0 0 H462 A205 207 0 0 1 462 414 H0 Z"/>
        </clipPath>
      </defs>
      <g clip-path="url(#card-outline)">
        <rect width="667" height="414" fill="var(--frost)"/>
        <rect class="band-top" x="0" y="0" width="667" height="117" fill="var(--vine-green)"/>
        <rect class="band-bottom" x="0" y="294" width="667" height="120" fill="var(--vine-green)"/>
        <circle cx="462" cy="207" r="207" fill="var(--frost)"/>
        <circle cx="462" cy="207" r="198" fill="var(--frost)" stroke="var(--frost-edge)" stroke-width="1"/>
      </g>
      <path class="rim" d="M462 2.5 A202.5 204.5 0 0 1 462 411.5" fill="none" stroke="var(--vine-green)" stroke-width="5"/>
    </svg>

    <div class="holder">
      <p class="holder-name">Dale Morton</p>
      <p class="holder-title">Managing Director</p>
    </div>

    <ul class="contacts">
      <li>
        <svg viewBox="0 0 24 24"><path d="M6.6 10.8a15.1 15.1 0 0 0 6.6 6.6l2.2-2.2a1 1 0 0 1 1-.25 11.4 11.4 0 0 0 3.6.57 1 1 0 0 1 1 1V20a1 1 0 0 1-1 1A17 17 0 0 1 3 4a1 1 0 0 1 1-1h3.5a1 1 0 0 1 1 1c0 1.25.2 2.45.57 3.6a1 1 0 0 1-.25 1z"/></svg>
        <span>805-219-6384</span>
      </li>
      <li>
        <svg viewBox="0 0 24 24"><path d="M2 5h20v14H2z M3 6.5 12 13l9-6.5" fill="var(--paper-white)" stroke="var(--vine-green)" stroke-width="1.6"/></svg>
        <span>info@vinehollowexcursions.example</span>
      </li>
      <li>
        <svg viewBox="0 0 24 24"><path d="M10 14a4 4 0 0 0 5.7 0l4-4a4 4 0 0 0-5.7-5.7l-1.2 1.2M14 10a4 4 0 0 0-5.7 0l-4 4a4 4 0 0 0 5.7 5.7l1.2-1.2" fill="none" stroke="var(--paper-white)" stroke-width="2.4" stroke-linecap="round"/></svg>
        <span>www.vinehollowexcursions.example</span>
      </li>
    </ul>

    <div class="brand">
      <span class="brand-dot"></span>
      <p class="brand-name">Vine Hollow<br>Excursions</p>
    </div>
  </div>
</body>
</html>
```